LIFE CHANGING NEW WEBSITE DESIGN NEEDED FOR FULL WEBSITE- FUN/FEMININE!

I need a website designed for a personal financial advice website geared at women called BLUE OTTER LANTERN. I will be providing free financial advice around topics of making, saving, spending and sharing money. The concept is to change the way women understand money and the necessity around building various passive income streams to ensure full financial freedom. This will then carry down to advice for mothers with children and children in particular. The website should be elegant and yet witty. I don't want lots of serious photos but more relatable. I will have a photo of myself and my story as this is a blog and needs to be relatable to women and mothers. I like pinks and greys. I want to have a pink piggy bank being broken with a hammer in the front screen to break our traditional mindset around piggy bank saving/spending habits. I have created a logo that is a pink piggy head with BLUE OTTER LANTERN that needs to be incorporated so that it blends into the heading. I have also already started designing the website on Squarespace and can provide access to that. Basically it should have a format of BLUE OTTER LANTERN LOGO center in header then on left hand navigation: MAKE, SAVE, SPEND, SHARE then on right hand header navigation: MISSION, GET STARTED, CONTACT BOL I would like to have the front page when you go to the url to have the image of the piggy bank being broken then a catchy phrase then under 4 boxes with MAKE (image and description) SAVE (image and description) SPEND (image and description) SHARE (image and description) if you click on those or the title they go to pages that are dedicated to each them. Each page should have a little intro on the topic then I want lots of blog links as I will be mainly writing blogs. Each blog site should have ability to write comments as well. I need social media icons on each page too. Please let me know what you need from me to get started. I prefer having a discussion if possible to not waste anyone's time. I need the site to be easy for me to use and add blogs/urls etc as needed. I also need the site to be put into my domain that I already purchased: www.blueotterlantern-sample.com

Target Market(s)

teenage girls, 20 something girls, 30 something girls and mothers

Coding

Coded - Design and coding required

Number of Pages Required

5+ page

Font styles to use
Sans Serif

Colors
e667a6
e34197
f59195
eea4c8
aaaaaa
cbcbcb
959595

Requirements
Must have
• TOP NAVIGATION
• MAKE SAVE SPEND SHARE LOGO/BLUE OTTER LANTERN MISSION GET STARTED CONTACT BOL
• FRONT PAGE: IMAGE OF PIGGY BANK BEING BROKEN WITH A HAMMER
• CATCH PHRASE OVER THE IMAGE
• BUTTON IN PINK- TAKE ACTION (WHICH DIRECTS TO TAKE ACTION TAB ON NAVIGATION HEADER
• 4 BOXES BELOW MAIN IMAGE WITH IMAGE/DESCRIPTIONS FOR MAKE, SAVE, SPEND, SHARE THAT EACH GO TO THE PAGES FROM THE NAVIGATION HEADER
• EACH PAGE SHOULD BE DEDICATED TO THOSE TOPICS THEN THERE IS AN INTRO ON EACH PAGE THEN THE LINKS TO DIFFERENT BLOGS AROUND EACH TOPIC FOR MAKE, SAVE, SPEND, SHARE
• EACH BLOG SHOULD HAVE COMMENTS SECTION AND SOCIAL MEDIA ICONS
• (GOOD TO USE PINKS/GREYS)
Should not have
• BE SUPER BUSY, CLUTTERED, FEEL LIKE I AM SELLING SOMETHING

```html
<!DOCTYPE html>
<html lang="en">
<head>
<meta charset="utf-8">
<title>Blue Otter Lantern</title>
<link href="https://fonts.googleapis.com/css2?family=Poppins:wght@400;500;600&family=Open+Sans:wght@400;600&display=swap" rel="stylesheet">
<style>
:root{
  --pink:#dc2a8a;
  --pink-soft:#e667a6;
  --pink-pale:#eea4c8;
  --ink:#333333;
  --text:#555555;
  --grey-light:#eeeeee;
  --grey-mid:#e2e2e2;
  --grey-icon:#aaaaaa;
  --footer:#2b2b2b;
  --white:#ffffff;
}
*{margin:0;padding:0;box-sizing:border-box}
html,body{width:1200px;height:2642px;overflow:hidden;background:var(--white)}
body{position:relative;font-family:"Open Sans",Arial,sans-serif;color:var(--text)}
a{text-decoration:none;color:inherit}
h1,h2,h3,p{font-weight:400}

/* header */
.site-header{position:absolute;left:0;top:0;width:1200px;height:54px;background:var(--white);z-index:3}
.nav{position:absolute;top:20px;display:flex;gap:31px;font-family:"Poppins",sans-serif;font-size:13px;color:var(--ink);text-transform:uppercase}
.nav-left{left:143px}
.nav-right{right:145px}
.nav .active{color:var(--pink)}
.brand-disc{position:absolute;left:461px;top:-118px;width:278px;height:278px;border-radius:50%;background:var(--white);z-index:2}
.brand{position:absolute;left:461px;top:15px;width:278px;text-align:center;z-index:4}
.brand-dot{width:42px;height:42px;border-radius:50%;background:var(--pink-pale);margin:0 auto 8px}
.brand-name{font-family:"Poppins",sans-serif;font-weight:400;font-size:24px;line-height:28px;color:var(--pink);white-space:nowrap}

/* hero */
.hero{position:absolute;left:0;top:54px;width:1200px;height:560px;overflow:hidden}
.hero-photo{position:absolute;inset:0;background:
  radial-gradient(ellipse 210px 150px at 720px 380px,rgba(222,98,150,.95),rgba(222,98,150,.6) 55%,transparent 100%),
  radial-gradient(ellipse 230px 110px at 880px 450px,rgba(214,80,110,.85),rgba(214,80,110,.35) 60%,transparent 100%),
  radial-gradient(ellipse 260px 40px at 800px 520px,rgba(70,74,82,.35),transparent 100%),
  radial-gradient(ellipse 60px 110px at 850px 110px,rgba(25,25,28,.95),rgba(25,25,28,.5) 60%,transparent 100%),
  radial-gradient(ellipse 170px 50px at 960px 230px,rgba(214,186,140,.85),transparent 100%),
  radial-gradient(ellipse 120px 150px at 1130px 320px,rgba(196,140,112,.9),rgba(196,140,112,.4) 60%,transparent 100%),
  linear-gradient(100deg,#6b727c 0%,#858d97 40%,#a2abb5 70%,#9aa2ab 100%)}
.hero-title{position:absolute;left:144px;top:210px;font-family:"Poppins",sans-serif;font-weight:600;font-size:29px;line-height:40px;color:var(--white);text-transform:uppercase}
.btn{display:inline-flex;align-items:center;justify-content:center;background:var(--pink);color:var(--white);border-radius:20px;font-family:"Poppins",sans-serif;font-size:13px;text-transform:uppercase}
.hero .btn{position:absolute;left:144px;top:299px;width:105px;height:40px}
.arrow{position:absolute;top:265px;width:22px;height:28px}

/* topic cards */
.topic{position:absolute;width:443px;height:178px;background:var(--grey-light);display:flex}
.topic-photo{width:159px;height:178px;flex:none}
.topic-body{padding:22px 16px 0 16px}
.topic-title{font-family:"Poppins",sans-serif;font-weight:600;font-size:24px;color:var(--pink);line-height:30px;text-transform:uppercase}
.topic-text{font-size:10.5px;line-height:16.5px;color:var(--ink);margin-top:4px}
.topic .btn{width:94px;height:34px;font-size:11px;margin-top:11px}

/* welcome */
.welcome{position:absolute;left:0;top:1156px;width:1200px;height:421px;background:var(--grey-light)}
.welcome-photo{position:absolute;left:600px;top:0;width:600px;height:421px;background:
  radial-gradient(ellipse 120px 70px at 140px 300px,rgba(60,70,55,.55),transparent 100%),
  radial-gradient(ellipse 110px 60px at 470px 360px,rgba(55,65,50,.55),transparent 100%),
  radial-gradient(ellipse 150px 80px at 330px 130px,rgba(232,232,210,.8),transparent 100%),
  radial-gradient(ellipse 140px 70px at 90px 90px,rgba(225,226,205,.7),transparent 100%),
  radial-gradient(ellipse 130px 70px at 500px 200px,rgba(220,222,200,.7),transparent 100%),
  linear-gradient(135deg,#b9bda3 0%,#8e987f 40%,#6e7b66 65%,#a9af97 100%)}
.welcome-title{position:absolute;left:144px;top:72px;font-family:"Poppins",sans-serif;font-weight:500;font-size:33px;line-height:40px;color:var(--pink)}
.welcome-text{position:absolute;left:144px;top:166px;width:392px;font-size:13px;line-height:24px;color:var(--text)}
.welcome-text em{font-style:normal;color:var(--pink)}
.welcome .btn{position:absolute;left:144px;top:303px;width:104px;height:40px}

/* blog */
.section-title{position:absolute;left:0;top:1650px;width:1200px;text-align:center;font-family:"Poppins",sans-serif;font-weight:500;font-size:33px;color:var(--pink)}
.post{position:absolute;top:1716px;width:440px;height:678px;background:var(--grey-light)}
.post-photo{height:280px}
.post-body{padding:18px 22px 0 22px;height:207px}
.post-title{font-family:"Poppins",sans-serif;font-weight:400;font-size:20px;line-height:23px;color:var(--pink)}
.post-date{font-family:"Poppins",sans-serif;font-size:13px;color:var(--ink);margin-top:11px}
.post-text{font-size:10.5px;line-height:18px;color:var(--text);margin-top:6px}
.post-text a{color:var(--pink)}
.share{display:flex;gap:8px;margin-top:10px}
.share span{width:24px;height:24px;border-radius:50%;background:var(--grey-icon)}
.comments{background:var(--grey-mid);height:191px;margin-top:2px;padding:8px}
.comment-box{height:80px;background:var(--white);font-size:10px;color:#777;padding:12px 13px}
.comment{position:relative;margin-top:12px;padding-left:58px}
.avatar{position:absolute;left:0;top:2px;width:48px;height:48px;border-radius:50%;background:linear-gradient(#d9c3b2,#b89a86)}
.comment-name{font-family:"Poppins",sans-serif;font-size:12px;color:var(--ink)}
.comment-text{font-size:9.5px;line-height:15px;color:var(--text);margin-top:3px}
.comment-links{font-size:9.5px;color:var(--text);margin-top:8px}
.view-all{position:absolute;left:524px;top:2426px;width:151px;height:40px}

/* footer */
.site-footer{position:absolute;left:0;top:2545px;width:1200px;height:97px;background:var(--footer)}
.footer-links{position:absolute;left:144px;top:26px;font-size:10.5px;color:#cccccc}
.footer-copy{position:absolute;left:144px;top:55px;font-size:10.5px;color:#cccccc}
.footer-social{position:absolute;left:997px;top:36px;display:flex;gap:7px}
.footer-social span{width:25px;height:25px;border-radius:50%;background:var(--pink-soft)}
</style>
</head>
<body>

<header class="site-header">
  <nav class="nav nav-left"><a class="active">Make</a><a>Save</a><a>Spend</a><a>Share</a></nav>
  <nav class="nav nav-right"><a>Mission</a><a>Get Started</a><a>Contact BOL</a></nav>
</header>
<div class="brand-disc"></div>
<div class="brand"><div class="brand-dot"></div><div class="brand-name">Blue Otter Lantern</div></div>

<section class="hero">
  <div class="hero-photo" role="img" aria-label="Pink piggy bank shattered by a hammer held in a hand, on a grey backdrop"></div>
  <h1 class="hero-title">Maecenas tortor accumsan<br>quam varius imperdiet</h1>
  <a class="btn">Read more</a>
  <svg class="arrow" style="left:50px" viewBox="0 0 22 28"><path d="M15 4 L6 14 L15 24" fill="none" stroke="#fff" stroke-width="3.5" stroke-linecap="round" stroke-linejoin="round"/></svg>
  <svg class="arrow" style="left:1127px" viewBox="0 0 22 28"><path d="M7 4 L16 14 L7 24" fill="none" stroke="#fff" stroke-width="3.5" stroke-linecap="round" stroke-linejoin="round"/></svg>
</section>

<article class="topic" style="left:144px;top:694px">
  <div class="topic-photo" role="img" aria-label="Stacks of coins around a compass" style="background:radial-gradient(ellipse 40px 30px at 40px 30px,rgba(200,200,205,.9),transparent),radial-gradient(ellipse 40px 25px at 125px 35px,rgba(190,190,195,.8),transparent),radial-gradient(ellipse 45px 45px at 110px 110px,rgba(210,205,190,.5),transparent),linear-gradient(160deg,#7c7b86,#3d3a48 55%,#1e1c26)"></div>
  <div class="topic-body"><h2 class="topic-title">Make</h2><p class="topic-text">Curabitur ac elit leo. In eleifend dui tellus, in sceler isque elit porttitor et. Integer eu massa lacinia, lacinia nulla non, volutpat purus.</p><a class="btn">Read more</a></div>
</article>
<article class="topic" style="left:612px;top:694px">
  <div class="topic-photo" role="img" aria-label="Hand dropping a coin into a silver piggy bank beside coin stacks" style="background:radial-gradient(ellipse 35px 40px at 100px 115px,rgba(225,228,232,.95),transparent),radial-gradient(ellipse 30px 35px at 40px 130px,rgba(150,100,60,.8),transparent),radial-gradient(ellipse 40px 25px at 100px 20px,rgba(220,180,160,.7),transparent),linear-gradient(180deg,#6f7072 0%,#8a8680 50%,#b28a5a 80%,#a07a4e)"></div>
  <div class="topic-body"><h2 class="topic-title">Save</h2><p class="topic-text">Curabitur ac elit leo. In eleifend dui tellus, in sceler isque elit porttitor et. Integer eu massa lacinia, lacinia nulla non, volutpat purus.</p><a class="btn">Read more</a></div>
</article>
<article class="topic" style="left:144px;top:898px">
  <div class="topic-photo" role="img" aria-label="Hand fanning colourful banknotes" style="background:radial-gradient(ellipse 45px 30px at 90px 25px,rgba(205,150,120,.9),transparent),linear-gradient(125deg,#d8706a 0%,#e9a59a 35%,#a9d3b2 60%,#5f8f78 78%,#1f1f1f 100%)"></div>
  <div class="topic-body"><h2 class="topic-title">Spend</h2><p class="topic-text">Curabitur ac elit leo. In eleifend dui tellus, in sceler isque elit porttitor et. Integer eu massa lacinia, lacinia nulla non, volutpat purus.</p><a class="btn">Read more</a></div>
</article>
<article class="topic" style="left:612px;top:898px">
  <div class="topic-photo" role="img" aria-label="Hands with a pen over a paper document" style="background:radial-gradient(ellipse 40px 30px at 45px 85px,rgba(205,160,140,.85),transparent),radial-gradient(ellipse 40px 30px at 115px 80px,rgba(200,155,135,.85),transparent),radial-gradient(ellipse 60px 30px at 80px 150px,rgba(250,252,255,.95),transparent),linear-gradient(180deg,#aebccf,#d6dde6 50%,#c0cad8)"></div>
  <div class="topic-body"><h2 class="topic-title">Share</h2><p class="topic-text">Curabitur ac elit leo. In eleifend dui tellus, in sceler isque elit porttitor et. Integer eu massa lacinia, lacinia nulla non, volutpat purus.</p><a class="btn">Read more</a></div>
</article>

<section class="welcome">
  <h2 class="welcome-title">Welcome to<br>Blue Otter Lantern (BOL)!</h2>
  <p class="welcome-text"><em>My mission is simple-</em> I want to challenge you to rethink the way you think about growing, spending and saving money. By rede-signing your life around your finances I want you to run your life as if you are the CEO of your own business, and the business is maximising the value and profitability of your life.</p>
  <a class="btn">Read more</a>
  <div class="welcome-photo" role="img" aria-label="Pile of scattered hundred-dollar banknotes"></div>
</section>

<h2 class="section-title">Blog</h2>

<article class="post" style="left:144px">
  <div class="post-photo" role="img" aria-label="Blurred businessman touching a glowing dollar sign on a digital screen" style="background:radial-gradient(ellipse 70px 90px at 330px 100px,rgba(240,230,220,.85),transparent),radial-gradient(ellipse 60px 70px at 320px 190px,rgba(215,170,150,.7),transparent),radial-gradient(ellipse 120px 160px at 110px 130px,rgba(40,70,120,.7),transparent),linear-gradient(135deg,#3a5a8c,#7190b8 50%,#2a4468)"></div>
  <div class="post-body">
    <h3 class="post-title">Maecenas vel tortor accumsan quam varius imperdiet</h3>
    <p class="post-date">18 June, 2019</p>
    <p class="post-text">Nam et tortor in ante iaculis porttitor in luctus mi. Vivamus gravida sem a pretium euismod. Nam lobortis, purus et fringilla tempus, risus eros dignissim diam, eget finibus sem risus sit amet eros. <a>More</a></p>
    <div class="share"><span></span><span></span><span></span><span></span><span></span></div>
  </div>
  <div class="comments">
    <div class="comment-box">Comments...</div>
    <div class="comment">
      <div class="avatar" role="img" aria-label="Commenter portrait"></div>
      <p class="comment-name">Peter Lane</p>
      <p class="comment-text">Sed egestas, nisl id cursus ultricies, turpis orci rhoncus odio, id tristique odio ex in lacus. Nam suscipit sapien eget blandit sollicitudin.</p>
      <p class="comment-links">Reply &nbsp;&nbsp;|&nbsp;&nbsp; Like &nbsp;&nbsp;|&nbsp;&nbsp; Comments</p>
    </div>
  </div>
</article>

<article class="post" style="left:615px">
  <div class="post-photo" role="img" aria-label="Man in a dark suit opening his shirt to reveal banknotes" style="background:radial-gradient(ellipse 55px 110px at 220px 150px,rgba(200,205,185,.95),rgba(200,205,185,.4) 70%,transparent),radial-gradient(ellipse 70px 130px at 220px 170px,rgba(240,240,240,.85),transparent),radial-gradient(ellipse 50px 30px at 150px 200px,rgba(190,150,130,.6),transparent),radial-gradient(ellipse 50px 30px at 290px 200px,rgba(190,150,130,.6),transparent),linear-gradient(180deg,#1a1a1c,#2e2e30 60%,#1e1e20)"></div>
  <div class="post-body">
    <h3 class="post-title">Fusce porta arcu mi, aliquet dictum nulla interdum</h3>
    <p class="post-date">18 June, 2019</p>
    <p class="post-text">Nam et tortor in ante iaculis porttitor in luctus mi. Vivamus gravida sem a pretium euismod. Nam lobortis, purus et fringilla tempus, risus eros dignissim diam, eget finibus sem risus sit amet eros. <a>More</a></p>
    <div class="share"><span></span><span></span><span></span><span></span><span></span></div>
  </div>
  <div class="comments">
    <div class="comment-box">Comments...</div>
    <div class="comment">
      <div class="avatar" role="img" aria-label="Commenter portrait" style="background:linear-gradient(#e6d3a8,#c9a97a)"></div>
      <p class="comment-name">Clara</p>
      <p class="comment-text">Sed egestas, nisl id cursus ultricies, turpis orci rhoncus odio, id tristique odio ex in lacus. Nam suscipit sapien eget blandit sollicitudin.</p>
      <p class="comment-links">Reply &nbsp;&nbsp;|&nbsp;&nbsp; Like &nbsp;&nbsp;|&nbsp;&nbsp; Comments</p>
    </div>
  </div>
</article>

<a class="btn view-all">View all articles</a>

<footer class="site-footer">
  <p class="footer-links">Make &nbsp;&nbsp;|&nbsp;&nbsp; Save &nbsp;&nbsp;|&nbsp;&nbsp; Spend &nbsp;&nbsp;|&nbsp;&nbsp; Share &nbsp;&nbsp;|&nbsp;&nbsp; Mission &nbsp;&nbsp;|&nbsp;&nbsp; Get Started &nbsp;&nbsp;|&nbsp;&nbsp; Contact BOL</p>
  <p class="footer-copy">Copyright &copy; 2019 &nbsp; BLUE OTTER LANTERN. &nbsp; All rights reserved.</p>
  <div class="footer-social"><span></span><span></span></div>
</footer>

</body>
</html>
```